Money Mindset Podcast needs fun, creative cover art

Launching a new podcast called 'Turning Your Thoughts Toward Savings' - aimed at an audience 30-50 who are interested in the practicalities of managing their money but also the more mental and emotional aspects.
Looking for something not too serious, warm and friendly.

Must be easy to read on phone screens
3000 x 3000 in size
Avoid currency symbols $, £ etc, as may have an international audience

Target Market(s)

Podcast listeners age 30-50 starting in the UK but then worldwide. Probably 60:40 female bias

Industry/Entity Type

Life Coaching

Font styles to use
Serif
Sans Serif

Colors
cadf82
fee18a
acd037
85cae6
eea4c8
f59195
85acd3

Requirements
Must have
• Simple, clear design. Easy to read on variety of devices. 3000 x 3000
Appeal to those with a spiritual or emotional interests
Nice to have
• Stand out among other money related podcasts
Maybe play around with clouds, lightbulbs and clearing skies
Should not have
• Currency symbols such as $ or £
Be too corporate or bank like
Stock images

```html
<!DOCTYPE html>
<html lang="en">
<head>
<meta charset="utf-8">
<title>Turning Your Thoughts Toward Savings — Podcast Cover</title>
<link rel="stylesheet" href="https://fonts.googleapis.com/css2?family=Andika:wght@400;700&display=swap">
<style>
  :root {
    --navy: #222d42;
    --sun-yellow: #ffde00;
    --burst-tone: #dfe6e4;
  }
  * { margin: 0; padding: 0; box-sizing: border-box; }
  html, body {
    width: 1200px;
    height: 1200px;
    overflow: hidden;
    background: var(--navy);
  }
  .cover {
    position: relative;
    width: 1200px;
    height: 1200px;
    background: var(--navy);
    overflow: hidden;
    font-family: "Andika", "Trebuchet MS", sans-serif;
    color: var(--sun-yellow);
  }
  .sunburst-area {
    position: absolute;
    inset: 0;
    background: radial-gradient(circle at 50% 50%,
      var(--navy) 0%, var(--navy) 52%,
      rgba(223, 230, 228, 0.10) 62%,
      rgba(223, 230, 228, 0.16) 78%,
      rgba(223, 230, 228, 0.08) 100%);
  }
  .title-block {
    position: absolute;
    left: 110px;
    top: 230px;
    width: 980px;
    height: 720px;
    transform: rotate(-8deg);
    transform-origin: 50% 50%;
  }
  .title-block span {
    position: absolute;
    white-space: nowrap;
    line-height: 1;
  }
  .title-lead {
    left: 70px;
    top: 40px;
    font-size: 74px;
    letter-spacing: 1px;
  }
  .title-main {
    left: 30px;
    top: 115px;
    font-size: 196px;
    letter-spacing: -2px;
  }
  .title-link {
    left: 850px;
    top: 150px;
    font-size: 62px;
    transform: rotate(90deg);
    transform-origin: 0 0;
    left: 948px;
    top: 60px;
  }
  .title-end {
    left: 40px;
    top: 345px;
    font-size: 214px;
    letter-spacing: -2px;
  }
</style>
</head>
<body>
  <main class="cover">
    <div class="sunburst-area" role="img" aria-label="Hand-drawn light sunburst strokes radiating around the title"></div>
    <h1 class="title-block">
      <span class="title-lead">turning your</span>
      <span class="title-main">thoughts</span>
      <span class="title-link">toward</span>
      <span class="title-end">savings</span>
    </h1>
  </main>
</body>
</html>
```